Research and Innovation programme/projects in WOOD based industries

1.Pramenova s.r.o. (offical registered brand name of our company)
-Managing technology development projects
-International cooperation and development European projects
Our company was founded in 2008 and started to work as a counsilary company operating in the section of european funds administrated by Czech republic. Nowadays we are specializing on projects in the sphere of science and research co-financed by EU.Since 6.6.2013 we are registered under European comission for a purpose of broad support of transnational projects.

Target Market(s)

We are primarily focused on european companies, which stand behind the latest research and innovation of sawing, planing, glulam and logging technologies based on wooden materials.

Coding

Coded - Design and coding required

Number of Pages Required

5+ page

Font styles to use
Serif

Colors
cadf82
abd037
9bcb3c
fee18a
ffcf3e
ffc214

Requirements
Must have
• The web will exist in three possible languages in czech, english and deutsch.
• First page : introduction of a company
• Second page : Area of expertise
• Third page: servicies our company provides
• Fourth page: Our partners
• Fifth page: Conditions of our servicies
• Sixth page: Succesful projects
• - we would also love if we had possibility to add videos about our successful projects
• Seventh: Our team
• We are serious company in the sphere of funds and counsilary servicies, that is why we would love to have web design as representative as possible
• Take on mind that that we are specializing on development management, try to apply that on your design
• In the section of contacts, we would love to have photos of our team,
• This is our current site: http://www.pramenova-example.eu/cz/partneri.html
• This is how our concurency sites are lookin. Take these designs as an slight inspiration.
• http://www.lumatrava-example.sk/en/
• https://www2.brenvick-example.com/global/en.html
Nice to have
• Visible logo on the front page for the visitor.
• As a inspiration we provided link for our current web design, but we dont want to copy the current style, just look at the logo and the pages that exists on current web.
• !!!!!!We also uploaded file, where we explain how our cooperation with partner works. Especially in the part 2. section of service. Take that as an ispiration too, or use that to understand, what our company do.
Should not have
• We are serious company in the sphere of funds and counsilary servicies, that is why we would love to have web design representative as possible

```html
<!DOCTYPE html>
<html lang="en">
<head>
<meta charset="utf-8">
<title>Pramenová – Research and Innovation Projects</title>
<link rel="stylesheet" href="https://fonts.googleapis.com/css2?family=Open+Sans:wght@400;600;700;800&display=swap">
<style>
:root{
  --green:#1a7f2e;
  --green-dark:#136a24;
  --orange:#f7900f;
  --ink:#111111;
  --text:#333333;
  --dark-band:#141414;
  --light-grey:#e2e0e0;
  --white:#ffffff;
}
*{margin:0;padding:0;box-sizing:border-box}
html,body{width:1200px;height:4535px;overflow:hidden}
body{font-family:"Open Sans",sans-serif;color:var(--text);background:var(--white);position:relative}
.wrap{position:absolute;left:98px;right:98px}
.section{position:absolute;left:0;width:1200px;overflow:hidden}
.btn{display:inline-block;background:var(--green);color:var(--white);font-weight:700;text-decoration:none;text-align:center}

/* header */
.site-header{top:0;height:113px;background:var(--white)}
.brand{position:absolute;left:98px;top:22px;display:flex;align-items:center;gap:12px}
.brand-mark{width:64px;height:64px;background:var(--green)}
.brand-name{font-size:31px;font-weight:700;color:var(--ink);letter-spacing:.5px}
.top-actions{position:absolute;right:98px;top:20px;display:flex;gap:6px}
.top-actions span{font-size:14px;font-weight:700;color:var(--white);padding:7px 24px}
.login{background:var(--green)}
.lang{background:var(--orange);padding:7px 14px!important}
.main-nav{position:absolute;right:98px;top:72px;display:flex;gap:25px;font-size:15px;font-weight:700;color:var(--ink)}

/* hero */
.hero{top:113px;height:647px}
.hero-photo{position:absolute;inset:0;background:linear-gradient(180deg,#6b5a48 0%,#8a6e50 40%,#5a4634 100%)}
.hero-box{position:absolute;left:326px;top:180px;width:552px;height:262px;background:rgba(30,30,30,.6);text-align:center;color:var(--white)}
.hero-box h1{font-size:62px;font-weight:700;margin-top:38px;letter-spacing:1px;line-height:1}
.hero-box p{font-size:21px;line-height:22px;margin-top:18px}
.hero-box .btn{font-size:20px;padding:13px 28px;margin-top:20px}
.hero-arrow{position:absolute;top:305px}

/* welcome */
.welcome{top:760px;height:598px}
.welcome h2{position:absolute;left:98px;top:80px;font-size:26px;font-weight:400;color:var(--ink);line-height:30px}
.welcome h2 b{font-weight:700;font-size:31px}
.welcome p{position:absolute;left:98px;top:175px;width:467px;font-size:15.5px;line-height:26px;text-align:justify;color:#222}
.welcome .btn{position:absolute;left:98px;top:472px;font-size:15px;padding:10px 30px}
.welcome svg{position:absolute;left:642px;top:80px}

/* expertise */
.expertise{top:1358px;height:469px;background:var(--dark-band)}
.section-title{text-align:center;font-weight:700;font-size:31px;color:var(--ink)}
.expertise .section-title{color:var(--white);margin-top:57px}
.cards{position:absolute;left:98px;top:150px;display:flex;gap:23px}
.card{width:319px;height:245px;position:relative}
.card span{position:absolute;left:0;bottom:0;background:rgba(20,20,20,.85);color:var(--white);font-weight:700;font-size:15px;padding:12px 40px}

/* services */
.services{top:1827px;height:665px}
.services .section-title{margin-top:82px;padding-right:29px}
.service-label{position:absolute;font-size:20px;font-weight:700;color:var(--ink);line-height:25px}
.service-label.left{text-align:right;right:806px}
.service-label.right{left:726px}
.icon-box{position:absolute;width:102px;height:78px;background:var(--green);display:flex;align-items:center;justify-content:center}

/* conditions */
.conditions{top:2492px;height:447px;background:#151515;text-align:center;color:var(--white)}
.conditions .section-title{color:var(--white);margin-top:62px}
.conditions p{width:900px;margin:30px auto 0;font-size:15.5px;line-height:26px}
.conditions .btn{font-size:15px;padding:14px 55px;margin-top:38px}

/* successful */
.projects{top:2939px;height:481px}
.projects-text{position:absolute;left:0;top:0;width:600px;height:481px;background:var(--orange)}
.projects-text h2{position:absolute;left:98px;top:53px;font-size:31px;color:var(--white);font-weight:700}
.projects-text ul{position:absolute;left:98px;top:115px;list-style:none}
.projects-text li{font-size:15.5px;color:var(--white);height:34px;display:flex;align-items:center;gap:8px}
.view-more{position:absolute;left:98px;top:373px;border:2px solid var(--green);color:var(--white);font-size:15px;padding:8px 30px}
.video{position:absolute;left:600px;top:0;width:600px;height:481px;background:linear-gradient(135deg,#5a5048,#a89a84 50%,#3f3a36)}
.video svg{position:absolute;left:250px;top:190px}

/* team */
.team{top:3420px;height:561px}
.team .section-title{margin-top:92px}
.member{position:absolute;top:157px;text-align:center;width:275px}
.member .photo{width:275px;height:250px;border:3px solid var(--orange)}
.member h3{font-size:20px;font-weight:700;color:var(--ink);margin-top:16px}
.member p{font-size:21px;color:#333;margin-top:2px}

/* partners */
.partners{top:3981px;height:285px;background:var(--light-grey)}
.partners .section-title{margin-top:48px}
.partner-row{position:absolute;left:98px;top:118px;display:flex;gap:22px}
.partner{width:320px;height:80px;background:var(--white);box-shadow:3px 3px 0 #555;display:flex;align-items:center;justify-content:center;text-align:center;font-weight:700;font-size:21px;color:var(--ink);line-height:20px}
.partner.small{font-size:19px}
.p-arrow{position:absolute;top:150px}

/* footer */
.site-footer{top:4266px;height:269px;background:#000;color:var(--white)}
.newsletter{position:absolute;left:168px;top:60px;font-size:24px;font-weight:700}
.nl-input{position:absolute;left:375px;top:62px;width:428px;height:48px;background:#eee;color:#333;font-size:15px;padding:12px 14px}
.nl-btn{position:absolute;left:803px;top:62px;width:192px;height:48px;background:var(--green);font-size:15px;font-weight:700;display:flex;align-items:center;justify-content:center}
.footer-rule{position:absolute;left:98px;right:98px;top:138px;border-top:1px solid #555}
.footer-nav{position:absolute;left:290px;top:167px;display:flex;gap:24px;font-size:15px;font-weight:700}
.socials{position:absolute;left:940px;top:160px;display:flex;gap:9px}
.socials span{width:33px;height:33px;border:2px solid var(--white);border-radius:50%}
.copyright{position:absolute;left:0;right:0;top:238px;text-align:center;font-size:15px}
</style>
</head>
<body>

<header class="section site-header">
  <div class="brand"><span class="brand-mark"></span><span class="brand-name">PRAMENOVÁ</span></div>
  <div class="top-actions"><span class="login">LOGIN</span><span class="lang">LANGUAGE ▾</span></div>
  <nav class="main-nav"><span>Home</span><span>About</span><span>Services</span><span>Our partners</span><span>Our Team</span><span>Contact</span></nav>
</header>

<section class="section hero">
  <div class="hero-photo" role="img" aria-label="Wood processing hall with stacked timber and sawing machinery"></div>
  <svg class="hero-arrow" style="left:20px" width="20" height="36" viewBox="0 0 20 36"><path d="M16 4 3 18l13 14" fill="none" stroke="#fff" stroke-width="2"/></svg>
  <svg class="hero-arrow" style="right:20px" width="20" height="36" viewBox="0 0 20 36"><path d="M4 4l13 14L4 32" fill="none" stroke="#fff" stroke-width="2"/></svg>
  <div class="hero-box">
    <h1>PRAMENOVÁ</h1>
    <p>Sed ut perspiciatis unde omnis iste natus<br>error sit voluptatem accusantium</p>
    <span class="btn">GET STARTED</span>
  </div>
</section>

<section class="section welcome">
  <h2>WELCOME TO<br><b>PRAMENOVÁ</b></h2>
  <p>Sed ut perspiciatis unde omnis iste natus error sit voluptatem accusantium doloremque laudantium, totam rem aperiam, eaque ipsa quae ab illo inventore veritatis et quasi architecto beatae vitae dicta sunt explicabo. Nemo enim ipsam voluptatem quia voluptas sit aspernatur aut odit aut fugit, sed quia consequuntur magni dolores eos qui ratione voluptatem sequi nesciunt. Neque porro quisquam est, qui dolorem ipsum quia dolor sit amet, consectetur adipisci velit, sed quia non numquam eius modi tempora incidunt ut labore et dolore magnam aliquam quaerat voluptatem. Ut enim ad minima veniam</p>
  <span class="btn">Read More</span>
  <svg width="470" height="440" viewBox="0 0 470 440">
    <polygon points="240,5 462,227 240,432" fill="none" stroke="#f7900f" stroke-width="9"/>
    <polygon points="228,10 8,220 228,430" fill="none" stroke="#1a7f2e" stroke-width="9"/>
    <defs><linearGradient id="wh" x1="0" y1="0" x2="0" y2="1"><stop offset="0" stop-color="#8c8f92"/><stop offset=".45" stop-color="#a09a92"/><stop offset="1" stop-color="#6e4a2c"/></linearGradient></defs>
    <polygon points="228,22 438,224 228,426 18,224" fill="url(#wh)" role="img" aria-label="Timber warehouse interior with stacked lumber"/>
  </svg>
</section>

<section class="section expertise">
  <h2 class="section-title">AREA OF EXPERTISE</h2>
  <div class="cards">
    <div class="card" role="img" aria-label="Classroom fitted with wooden furniture" style="background:linear-gradient(180deg,#c9ccd0,#7d7468 60%,#b8a888)"><span>LOREM IPSUM</span></div>
    <div class="card" role="img" aria-label="Timber roof frame under construction against the sky" style="background:linear-gradient(180deg,#7fa8d8,#cfd9e6 45%,#c89050)"><span>LOREM IPSUM</span></div>
    <div class="card" role="img" aria-label="Reception interior with wooden wall panelling" style="background:linear-gradient(90deg,#5a4030,#b48a62 50%,#d9c4a8)"><span>LOREM IPSUM</span></div>
  </div>
</section>

<section class="section services">
  <h2 class="section-title">OUR SERVICES</h2>
  <div class="service-label left" style="top:186px">PROJECT<br>COORDINATION</div>
  <div class="service-label left" style="top:289px">PROJECT<br>FINANCING</div>
  <div class="service-label left" style="top:383px">TECHNOLOGY AND<br>FOREIGN TRADE PROJECTS</div>
  <div class="service-label right" style="top:186px">PROJECTS IN THE FRAMEWORK OF<br>INTERNATIONAL COOPERATION</div>
  <div class="service-label right" style="top:285px">EU PROJECTS</div>
  <div class="service-label right" style="top:378px">INTERNATIONAL DEVELOPMENT<br>PROJECTS</div>
  <div class="icon-box" style="left:436px;top:167px"><svg width="40" height="40" viewBox="0 0 40 40" fill="none" stroke="#fde06a" stroke-width="2"><circle cx="20" cy="8" r="4"/><path d="M20 12v8M8 20h24M8 20v6M20 20v6M32 20v6"/><circle cx="8" cy="30" r="3"/><circle cx="20" cy="30" r="3"/><circle cx="32" cy="30" r="3"/></svg></div>
  <div class="icon-box" style="left:590px;top:167px"><svg width="40" height="40" viewBox="0 0 40 40" fill="none" stroke="#fde06a" stroke-width="2"><path d="M4 18l8-6 8 4 8-4 8 6-10 10-6-4-6 4z"/></svg></div>
  <div class="icon-box" style="left:436px;top:270px"><svg width="40" height="40" viewBox="0 0 40 40" fill="none" stroke="#fde06a" stroke-width="2"><circle cx="20" cy="14" r="8"/><path d="M20 10v8M6 24c4 0 8 8 14 8s10-8 14-8"/></svg></div>
  <div class="icon-box" style="left:590px;top:270px"><svg width="40" height="40" viewBox="0 0 40 40" fill="none" stroke="#fde06a" stroke-width="2"><rect x="10" y="6" width="22" height="28"/><path d="M14 14h14M14 20h14M14 26h8"/></svg></div>
  <div class="icon-box" style="left:436px;top:364px"><svg width="40" height="40" viewBox="0 0 40 40" fill="none" stroke="#fde06a" stroke-width="2"><circle cx="20" cy="16" r="9"/><path d="M16 30h8M17 34h6"/></svg></div>
  <div class="icon-box" style="left:590px;top:364px"><svg width="40" height="40" viewBox="0 0 40 40" fill="none" stroke="#fde06a" stroke-width="2"><path d="M6 34h28M10 34v-8M17 34v-12M24 34v-6M31 34v-14"/><circle cx="12" cy="10" r="4"/><circle cx="28" cy="8" r="3"/></svg></div>
  <div class="icon-box" style="left:519px;top:458px"><svg width="40" height="40" viewBox="0 0 40 40" fill="none" stroke="#fde06a" stroke-width="2"><circle cx="12" cy="26" r="5"/><circle cx="28" cy="12" r="5"/><circle cx="24" cy="30" r="4"/><path d="M16 23l8-8M16 28l4 1"/></svg></div>
  <div class="service-label" style="left:473px;top:560px">EXPORT PROMOTION</div>
</section>

<section class="section conditions">
  <h2 class="section-title">CONDITIONS OF OUR SERVICES</h2>
  <p>Sed ut perspiciatis unde omnis iste natus error sit voluptatem accusantium doloremque laudantium, totam rem aperiam, eaque ipsa quae ab illo inventore veritatis et quasi architecto beatae vitae dicta sunt explicabo Nemo enim ipsam voluptatem quia voluptas sit aspernatur aut odit aut fugit, sed quia consequuntur magni dolores eos qui ratione voluptatem sequi nesciunt. Neque porro quisquam est, qui dolorem ipsum quia dolor sit amet</p>
  <span class="btn">Contact Us</span>
</section>

<section class="section projects">
  <div class="projects-text">
    <h2>SUCCESSFUL PROJECTS</h2>
    <ul>
      <li>→ Nemo enim ipsam voluptatem quia voluptas sit</li>
      <li>→ Nemo enim ipsam voluptatem quia voluptas sit</li>
      <li>→ Nemo enim ipsam voluptatem quia voluptas sit</li>
      <li>→ Nemo enim ipsam voluptatem quia voluptas sit</li>
      <li>→ Nemo enim ipsam voluptatem quia voluptas sit</li>
      <li>→ Nemo enim ipsam voluptatem quia voluptas sit</li>
      <li>→ Nemo enim ipsam voluptatem quia voluptas sit</li>
    </ul>
    <span class="view-more">View More</span>
  </div>
  <div class="video" role="img" aria-label="Video still of carpenters working a wooden panel on a machine">
    <svg width="100" height="100" viewBox="0 0 100 100" fill="none" stroke="#fff" stroke-width="4"><circle cx="50" cy="50" r="46"/><path d="M40 30v40l30-20z"/></svg>
  </div>
</section>

<section class="section team">
  <h2 class="section-title">OUR TEAM</h2>
  <div class="member" style="left:158px"><div class="photo" role="img" aria-label="Portrait photo of team member" style="background:linear-gradient(180deg,#6b6a66,#8a7c70)"></div><h3>TOMÁŠ BREZINA</h3><p>Geschäftsführer</p></div>
  <div class="member" style="left:454px"><div class="photo" role="img" aria-label="Portrait photo of team member" style="background:linear-gradient(180deg,#e8e0dc,#b89a88)"></div><h3>MGR.LENKA HORÁKOVÁ</h3><p>Projekt manager</p></div>
  <div class="member" style="left:767px"><div class="photo" role="img" aria-label="Portrait photo of team member" style="background:linear-gradient(90deg,#d8d8d6,#9a9894)"></div><h3>MAREK SEDLÁK</h3><p>Projekt manager</p></div>
</section>

<section class="section partners">
  <h2 class="section-title">OUR PARTNERS</h2>
  <svg class="p-arrow" style="left:36px" width="16" height="28" viewBox="0 0 16 28"><path d="M13 3 3 14l10 11" fill="none" stroke="#222" stroke-width="2"/></svg>
  <div class="partner-row">
    <div class="partner">Moravalink</div>
    <div class="partner">Vltavex Trade</div>
    <div class="partner small">Elbe-Moldau<br>Wirtschaftsverband</div>
  </div>
  <svg class="p-arrow" style="right:36px" width="16" height="28" viewBox="0 0 16 28"><path d="M3 3l10 11L3 25" fill="none" stroke="#222" stroke-width="2"/></svg>
</section>

<footer class="section site-footer">
  <div class="newsletter">NEWSLETTER</div>
  <div class="nl-input">Enter your email</div>
  <div class="nl-btn">SUBSCRIBE</div>
  <div class="footer-rule"></div>
  <nav class="footer-nav"><span>Home</span><span>About</span><span>Services</span><span>Successful Projects</span><span>Our Team</span><span>Contact</span></nav>
  <div class="socials"><span></span><span></span><span></span><span></span></div>
  <div class="copyright">Copyrights © 2019 All Rights Reserved</div>
</footer>

</body>
</html>
```